MRT Property - Business Cards

Looking for a business card & general letterhead, signage etc design for our new logo.

Colours:
000a20
0056a2
00b5ef
0088ce
68cef2

Fonts:
Poppins
Karla

Please keep look and feel of new brand - example in the zip package I sent.

```html
<!DOCTYPE html>
<html lang="en">
<head>
<meta charset="UTF-8">
<title>MRT Property – Business Cards</title>
<link rel="stylesheet" href="https://fonts.googleapis.com/css2?family=Montserrat:wght@400;500;700&display=swap">
<style>
  :root {
    --navy: #000a20;
    --card-dark: #0e1428;
    --brand-blue: #0056a2;
    --sky: #00b5ef;
    --mid-blue: #0088ce;
    --pale-blue: #68cef2;
    --ink: #1e2230;
    --paper: #ffffff;
    --backdrop: #3b3b3d;
  }
  * { margin: 0; padding: 0; box-sizing: border-box; }
  html, body { width: 1200px; height: 689px; overflow: hidden; }
  body {
    background: var(--backdrop);
    font-family: "Montserrat", sans-serif;
    position: relative;
  }
  .card {
    position: absolute;
    top: 194px;
    width: 520px;
    height: 300px;
    overflow: hidden;
  }
  .card--front { left: 50px; background: var(--card-dark); }
  .card--back { left: 630px; background: var(--paper); }

  .brand-name {
    font-family: "Montserrat", sans-serif;
    font-weight: 700;
    color: var(--brand-blue);
    white-space: nowrap;
    letter-spacing: 1px;
  }
  .card--front .brand-name {
    position: absolute;
    left: 0; right: 0; top: 118px;
    text-align: center;
    font-size: 52px;
  }
  .card--back .brand-name {
    position: absolute;
    right: 40px; top: 34px;
    font-size: 30px;
  }

  .holder { position: absolute; left: 34px; top: 118px; }
  .holder__name {
    font-weight: 700;
    font-size: 22px;
    color: var(--brand-blue);
    letter-spacing: 0.5px;
  }
  .holder__role {
    font-weight: 400;
    font-size: 12px;
    color: var(--ink);
    letter-spacing: 0.6px;
    margin-top: 2px;
  }
  .divider {
    position: absolute;
    left: 34px; right: 34px; top: 178px;
    height: 1px;
    background: var(--ink);
  }
  .contacts {
    position: absolute; left: 34px; top: 190px;
    list-style: none;
    font-size: 12.5px; color: var(--ink);
  }
  .contacts li { display: flex; align-items: center; gap: 8px; height: 20px; }
  .contacts svg { width: 12px; height: 12px; fill: var(--mid-blue); }
  .address {
    position: absolute; right: 34px; top: 192px;
    text-align: right; font-size: 12.5px; color: var(--ink); line-height: 20px;
  }
  .footer-band { position: absolute; left: 0; bottom: 0; width: 520px; height: 58px; }
  .web {
    position: absolute; right: 20px; bottom: 14px;
    font-size: 12.5px; color: var(--paper); letter-spacing: 0.3px;
  }
</style>
</head>
<body>
  <section class="card card--front" aria-label="Business card front">
    <span class="brand-name">MRT Property</span>
  </section>

  <section class="card card--back" aria-label="Business card back">
    <span class="brand-name">MRT Property</span>

    <div class="holder">
      <p class="holder__name">DANIEL HART</p>
      <p class="holder__role">MANAGING DIRECTOR</p>
    </div>

    <div class="divider"></div>

    <ul class="contacts">
      <li><svg viewBox="0 0 24 24"><path d="M6.6 10.8a15 15 0 0 0 6.6 6.6l2.2-2.2a1 1 0 0 1 1-.25 11.4 11.4 0 0 0 3.6.57 1 1 0 0 1 1 1V20a1 1 0 0 1-1 1A17 17 0 0 1 3 4a1 1 0 0 1 1-1h3.5a1 1 0 0 1 1 1c0 1.25.2 2.45.57 3.6a1 1 0 0 1-.25 1z"/></svg>044-987 654 321</li>
      <li><svg viewBox="0 0 24 24"><path d="M2 5h20v14H2zm2 2v.5l8 5 8-5V7l-8 5z"/></svg>info@mrtprop.com</li>
    </ul>

    <p class="address">421, Address line goes here<br>45452, Country name</p>

    <svg class="footer-band" viewBox="0 0 520 58" aria-hidden="true">
      <polygon points="0,40 330,40 346,24 520,24 520,28 348,28 332,44 0,44" fill="var(--mid-blue)"/>
      <polygon points="0,50 336,50 352,34 520,34 520,58 0,58" fill="var(--brand-blue)"/>
    </svg>
    <span class="web">www.mrtproperty.com</span>
  </section>
</body>
</html>
```